Marlow Estate Fixers (Handyman / Home Improvement Company)

Looking for a double sided professional looking business card with Logo attached to be highlighted on one side and throwing in an image of a handyman as an option would be nice to see as well. We are a company focused on providing quality Handyman and Home improvement services in a timely manner that is done right the first time with integrity

Industry/Entity Type

Handyman / Home Improvement

Contact Information for Business Card

(LOGO, Name, Mobile and office phone numbers, email) on front side of card, (the words "The SOLUTION to all of your Handyman and Home Improvement needs" followed by "Family Owned and Operated" at the very bottom) on the back.

Colors
EB3D1F
EC4F4E
F09395
F8D3D4
FCEDEE

Requirements
Must have
• Red, Gray, Black Color scheme
Should not have
• No Yellow or Blue colors

```html
<!DOCTYPE html>
<html lang="en">
<head>
<meta charset="utf-8">
<title>Marlow Estate Fixers — Business Card</title>
<link href="https://fonts.googleapis.com/css2?family=Bebas+Neue&family=Montserrat:wght@800;900&family=Poppins:ital,wght@0,400;1,400&display=swap" rel="stylesheet">
<style>
  :root {
    --bg: #3a3a3c;
    --card: #000000;
    --red: #eb3d1f;
    --red-soft: #ec4f4e;
    --white: #ffffff;
    --line: #8a8a8a;
    --art-top: #c9692d;
    --art-bottom: #4a5f85;
  }
  * { box-sizing: border-box; margin: 0; padding: 0; }
  html, body { width: 1200px; height: 689px; overflow: hidden; }
  body {
    background: var(--bg);
    position: relative;
    font-family: "Poppins", sans-serif;
  }
  .card {
    position: absolute;
    top: 190px;
    width: 540px;
    height: 310px;
    background: var(--card);
    border-radius: 18px;
    border-bottom: 3px solid var(--red);
    border-left: 2px solid var(--red);
    overflow: hidden;
  }
  .card--back { left: 40px; }
  .card--front { left: 620px; }

  /* Back side */
  .handyman-art {
    position: absolute;
    left: 40px;
    top: 24px;
    width: 170px;
    height: 286px;
    border-radius: 80px 80px 6px 6px;
    background: linear-gradient(180deg, var(--art-top) 0%, #7a4a3a 45%, var(--art-bottom) 100%);
    opacity: 0.85;
  }
  .tagline {
    position: absolute;
    left: 232px;
    top: 62px;
    font-family: "Bebas Neue", sans-serif;
    line-height: 1;
  }
  .tagline__lead { color: var(--red); font-size: 30px; letter-spacing: 0.5px; }
  .tagline__main { color: var(--white); font-size: 44px; letter-spacing: 0.5px; margin-top: 4px; }
  .tagline__main span { display: block; }
  .family-note {
    position: absolute;
    right: 34px;
    bottom: 28px;
    color: var(--white);
    font-style: italic;
    font-size: 15px;
    letter-spacing: 0.5px;
  }

  /* Front side */
  .brand {
    position: absolute;
    top: 44px;
    left: 0;
    right: 0;
    display: flex;
    justify-content: center;
    align-items: center;
    gap: 12px;
  }
  .brand__dot { width: 22px; height: 22px; border-radius: 50%; background: var(--red); }
  .brand__name {
    font-family: "Montserrat", sans-serif;
    font-weight: 900;
    font-size: 26px;
    color: var(--white);
    letter-spacing: 1px;
  }
  .person-name {
    position: absolute;
    top: 128px;
    left: 0; right: 0;
    text-align: center;
    font-family: "Montserrat", sans-serif;
    font-weight: 900;
    font-size: 34px;
    letter-spacing: 3px;
    color: var(--red);
  }
  .contact-rule {
    position: absolute;
    top: 208px;
    left: 40px;
    right: 40px;
    height: 1px;
    background: var(--line);
  }
  .contact-list {
    position: absolute;
    top: 194px;
    left: 20px;
    right: 20px;
    display: flex;
    justify-content: space-between;
    list-style: none;
  }
  .contact-item {
    width: 160px;
    display: flex;
    flex-direction: column;
    align-items: center;
    gap: 12px;
    color: var(--white);
    font-size: 15px;
  }
  .contact-item--email { width: 180px; font-size: 14px; }
  .contact-icon {
    width: 28px; height: 28px;
    border-radius: 50%;
    background: var(--red-soft);
    display: flex; align-items: center; justify-content: center;
    border: 4px solid var(--card);
    box-sizing: content-box;
  }
  .contact-icon svg { width: 14px; height: 14px; }
</style>
</head>
<body>

<section class="card card--back" aria-label="Card back">
  <div class="handyman-art" role="img" aria-label="Illustration of a friendly handyman in hard hat, safety vest and tool belt, arms crossed"></div>
  <h1 class="tagline">
    <span class="tagline__lead">Your solution to all of your</span>
    <span class="tagline__main"><span>Handyman and home</span><span>improvement needs</span></span>
  </h1>
  <p class="family-note">Family Owned and Operated</p>
</section>

<section class="card card--front" aria-label="Card front">
  <div class="brand">
    <span class="brand__dot"></span>
    <span class="brand__name">MARLOW ESTATE FIXERS</span>
  </div>
  <h2 class="person-name">DANIEL HARGROVE</h2>
  <div class="contact-rule"></div>
  <ul class="contact-list">
    <li class="contact-item">
      <span class="contact-icon">
        <svg viewBox="0 0 14 14" fill="none" stroke="#fff" stroke-width="1.4"><rect x="3.5" y="1" width="7" height="12" rx="1.2"/><line x1="6" y1="11" x2="8" y2="11"/></svg>
      </span>
      <span>044-555 018 274</span>
    </li>
    <li class="contact-item contact-item--email">
      <span class="contact-icon">
        <svg viewBox="0 0 14 14" fill="#fff"><path d="M1 3h12v8H1z"/><path d="M1 3l6 5 6-5" fill="none" stroke="#ec4f4e" stroke-width="1.2"/></svg>
      </span>
      <span>hello@marlowfixers.com</span>
    </li>
    <li class="contact-item">
      <span class="contact-icon">
        <svg viewBox="0 0 14 14" fill="#fff"><path d="M3 1.5l2.2 2.6-1.1 1.6a7 7 0 0 0 4.2 4.2l1.6-1.1 2.6 2.2-1.3 1.8C6.2 12.6 1.4 7.8 1.2 2.8z"/></svg>
      </span>
      <span>044-555 018 275</span>
    </li>
  </ul>
</section>

</body>
</html>
```